IT Company that provides secure IT solutions and services to our customers

We need business cards and a logo for a new IT Solutions company just created based in Kuala Lumpur, Malaysia. But will also be serving other countries in the region. We provide secure data, voice solutions on mobile platforms. Our first offering is encrypted voice and data solutions for IOS, Android, Windows and BlackBerry devices.

Target Market(s)

large organizations Govt, Police, Defence, Anti-corruption, Legal, highly regulated industries such as Health-care, Financial, Banking, Insurance,

Industry/Entity Type

Information Technology

Contact Information for Business Card

VelmoraNet (Logo - colour is ORVEX blue)Roshan Adeel Managing Director Kryption IT Sdn. Bhd.5th Floor, Block D, Wisma PLB,No.14 Jalan Seri Melor,50470, Kuala LumpurMalaysia

Font styles to use
Sans Serif

Colors
3176b5
ec1f27
fbed22

Requirements
Must have
• VelmoraNet all in Blue like ORVEX blue. A logo design perhaps a play of VN, K with a dangling T (colour can be any)
Nice to have
• I want a clean crisp card, not too busy, easy to read.

```html
<!DOCTYPE html>
<html lang="en">
<head>
<meta charset="utf-8">
<title>VelmoraNet Business Cards</title>
<link rel="stylesheet" href="https://fonts.googleapis.com/css2?family=PT+Sans:wght@400;700&display=swap">
<style>
  :root {
    --backdrop: #ecebe8;
    --card: #ffffff;
    --brand-blue: #1f5aa6;
    --ink: #1c1c1c;
    --pattern-tone: #e9eef5;
    --edge-shadow: rgba(0, 0, 0, 0.18);
  }
  * { margin: 0; padding: 0; box-sizing: border-box; }
  html, body {
    width: 1200px;
    height: 900px;
    overflow: hidden;
    background: var(--backdrop);
    font-family: "PT Sans", sans-serif;
  }
  .canvas {
    position: relative;
    width: 1200px;
    height: 900px;
  }
  .card {
    position: absolute;
    width: 630px;
    height: 360px;
    background: var(--card);
    box-shadow: 0 6px 18px var(--edge-shadow);
    overflow: hidden;
  }
  /* Card back */
  .card-back {
    left: 110px;
    top: 110px;
  }
  .card-back .pattern-field {
    position: absolute;
    inset: 0;
    background: linear-gradient(135deg, var(--pattern-tone) 0%, #f3f6fa 100%);
  }
  .card-back .back-wordmark {
    position: absolute;
    right: 30px;
    bottom: 28px;
    padding: 4px 10px 4px 14px;
    background: var(--card);
    color: var(--brand-blue);
    font-weight: 700;
    font-size: 52px;
    letter-spacing: 0.5px;
    line-height: 1;
  }
  /* Card front */
  .card-front {
    left: 460px;
    top: 430px;
  }
  .brand-lockup {
    position: absolute;
    left: 40px;
    top: 40px;
    display: flex;
    align-items: center;
    gap: 14px;
  }
  .brand-square {
    width: 50px;
    height: 50px;
    border: 3px solid var(--brand-blue);
  }
  .brand-name {
    color: var(--brand-blue);
    font-weight: 700;
    font-size: 46px;
    line-height: 1;
  }
  .contact-block {
    position: absolute;
    left: 360px;
    top: 140px;
    width: 250px;
    color: var(--ink);
  }
  .person-name {
    color: var(--brand-blue);
    font-weight: 700;
    font-size: 17px;
    line-height: 1.1;
  }
  .person-title {
    font-size: 14px;
    line-height: 1.3;
  }
  .company-name {
    margin-top: 40px;
    color: var(--brand-blue);
    font-weight: 700;
    font-size: 17px;
    line-height: 1.1;
  }
  .company-address {
    font-style: normal;
    font-size: 15px;
    line-height: 1.3;
  }
</style>
</head>
<body>
  <main class="canvas">
    <section class="card card-back" aria-label="Business card back">
      <div class="pattern-field" role="img" aria-label="Faint repeating brand mark pattern across the card back"></div>
      <p class="back-wordmark">VelmoraNet</p>
    </section>

    <section class="card card-front" aria-label="Business card front">
      <div class="brand-lockup">
        <span class="brand-square" aria-hidden="true"></span>
        <span class="brand-name">VelmoraNet</span>
      </div>
      <div class="contact-block">
        <p class="person-name">Roshan Adeel</p>
        <p class="person-title">Managing Director</p>
        <p class="company-name">Velmora Net</p>
        <address class="company-address">Sdn. Bhd.5th Floor, Block D, Wisma PLB,No.14 Jalan Seri Melor, 50470, Kuala Lumpur Malaysia</address>
      </div>
    </section>
  </main>
</body>
</html>
```